Book cover for book about Climate Change

Looking for a clean, bold, and attractive cover for a mass-market paperback (5.5"x 8.5") about solving the climate change problem. Title is either "Where the Rivers Meet” or A Harbor Made of Glass” (your choice), subtitle is "A practical field guide to mending the weather — so that the young ones after us inherit steady seasons and open skies," author is Lorne Whitcombe. Thinking that it *might* feature an image of Earth (or a portion thereof) and its very thin layer of atmosphere -- but STRONGLY encourage other ideas too!

Requirements
Nice to have
• Keep it positive — NOT scary doom-and-gloom

```html
<!DOCTYPE html>
<html lang="en">
<head>
<meta charset="utf-8">
<title>Where the Rivers Meet — Lorne Whitcombe</title>
<link rel="stylesheet" href="https://fonts.googleapis.com/css2?family=Teko:wght@500&family=Archivo+Narrow:wght@700&family=Archivo:wght@400&display=swap">
<style>
  :root {
    --paper: #ffffff;
    --ink: #0b0b0b;
    --leaf: #1db52a;
    --leaf-pale: #b9dfa0;
    --ocean-deep: #1c3d84;
    --ocean-mid: #4a72b8;
    --cloud: #e9eef6;
    --skin: #e8b79a;
  }
  html, body {
    margin: 0;
    padding: 0;
    width: 800px;
    height: 1200px;
    overflow: hidden;
    background: var(--paper);
  }
  .cover {
    position: relative;
    width: 800px;
    height: 1200px;
    background: var(--paper);
    overflow: hidden;
  }
  .title {
    position: absolute;
    left: 0;
    top: 66px;
    width: 800px;
    margin: 0;
    text-align: center;
    font-family: "Teko", "Arial Narrow", sans-serif;
    font-weight: 500;
    text-transform: uppercase;
    line-height: 0.82;
  }
  .title-line {
    display: block;
    white-space: nowrap;
  }
  .title-line--fade {
    font-size: 186px;
    letter-spacing: 1px;
    background: linear-gradient(to bottom, var(--ink) 30%, var(--leaf-pale) 92%);
    -webkit-background-clip: text;
    background-clip: text;
    color: transparent;
  }
  .title-line--solid {
    font-size: 154px;
    letter-spacing: 0;
    color: var(--ink);
    margin-top: 14px;
  }
  .subtitle {
    position: absolute;
    left: 0;
    top: 456px;
    width: 800px;
    margin: 0;
    text-align: center;
    text-transform: uppercase;
  }
  .subtitle-lead {
    display: block;
    font-family: "Archivo Narrow", "Arial Narrow", sans-serif;
    font-weight: 700;
    font-size: 17px;
    letter-spacing: 4.4px;
    color: var(--leaf);
    margin-bottom: 16px;
    white-space: nowrap;
  }
  .subtitle-rest {
    display: block;
    font-family: "Archivo", Arial, sans-serif;
    font-weight: 400;
    font-size: 17px;
    letter-spacing: 2.6px;
    line-height: 28px;
    color: var(--ink);
  }
  .cover-art {
    position: absolute;
    left: 0;
    top: 590px;
    width: 800px;
    height: 420px;
  }
  .author {
    position: absolute;
    left: 0;
    top: 1072px;
    width: 800px;
    margin: 0;
    text-align: center;
    font-family: "Archivo Narrow", "Arial Narrow", sans-serif;
    font-weight: 700;
    font-size: 64px;
    line-height: 1;
    letter-spacing: 7px;
    color: var(--leaf);
    text-transform: uppercase;
    white-space: nowrap;
  }
</style>
</head>
<body>
  <main class="cover">
    <h1 class="title">
      <span class="title-line title-line--fade">Where the</span>
      <span class="title-line title-line--solid">Rivers Meet</span>
    </h1>

    <p class="subtitle">
      <span class="subtitle-lead">A practical field guide to mending the weather</span>
      <span class="subtitle-rest">So that the young ones after us inherit<br>steady seasons and open skies</span>
    </p>

    <svg class="cover-art" viewBox="0 0 800 420" role="img" aria-label="Photograph of an adult hand holding planet Earth while a small child's hand reaches out to touch it">
      <defs>
        <radialGradient id="earth-glow" cx="0.5" cy="0.5" r="0.5">
          <stop offset="0" stop-color="var(--cloud)"/>
          <stop offset="0.35" stop-color="var(--ocean-mid)"/>
          <stop offset="0.75" stop-color="var(--ocean-deep)"/>
          <stop offset="0.95" stop-color="var(--skin)" stop-opacity="0.35"/>
          <stop offset="1" stop-color="var(--paper)" stop-opacity="0"/>
        </radialGradient>
      </defs>
      <rect x="0" y="0" width="800" height="420" fill="url(#earth-glow)"/>
    </svg>

    <p class="author">Lorne Whitcombe</p>
  </main>
</body>
</html>
```